Belvascotravel.com web design project + logo design

Hi,

We are a Russian online tour operator - sunkettle.com

We are looking to tranmsfer our domain to belvascotravel.com. The website and logo need to be belvascoesque - we are not looking to change our functionality, but we need to make the website much more attracitve to clients, much more wild looking but at the same time remaining a professional travel company.

The main concept of the website should be innovative travel (as belvasco was an innovator). Alternatively, you could go down the artist route and go down the draw / design your own tour road.

On our website the customer is able to combine travel services (hotels, flights, Visa services, and soon chauffeur, car rental etc...) put it into their basket (the basket definitely has to look better than it is at the moment) and pay for it in one go by card.

We are also stressin our customer support with web chat, call centre etc... (call centre number at the top of the page)

We aim to provide an easy user experience, but we need to make it have some more style, so I will be waiting for what you guys can come up with.
Let me know if you have any questions - skype is: mrdolbarin

Industry/Entity Type

It Company

Requirements
Must have
• It is quite a simple task - to take the existing website sunkettle.com and belvascosize it to create belvascotravel.com, the functionality of the website will remain the same and there are not many pages in the website. Homepage, Checkout step1, Checkout step 2 (you can view both of these if you select a service) and the generic pages for T&C''s, Privacy policy etc...

IMPORTANT UPDATE

We are also looking at how the search results will look in the designs, (please do a search on our website for hotel / flight)

```html
<!DOCTYPE html>
<html lang="en">
<head>
<meta charset="utf-8">
<title>Belvasco Travel</title>
<link href="https://fonts.googleapis.com/css2?family=PT+Sans:wght@400;700&family=PT+Sans+Narrow:wght@400;700&display=swap" rel="stylesheet">
<style>
:root{
  --sky-top:#2a63c4;--sky-mid:#4d8fdc;--sea:#1d58b4;--deep:#16468f;
  --frame:#8fb3dc;--white:#fff;--text:#333;--muted:#555;
  --orange:#f39a12;--orange-dark:#e57f00;--cyan:#2a9ad8;
  --navy:#1c2f86;--nav:#111;--nav-active:#1e57b8;
  --green:#6cb52a;--green-dark:#3f8a0f;--basket:#3f7fd0;
  --footer:#1b4b9c;--footer-dark:#214f9f;--line:#d6d6d6;
}
*{margin:0;padding:0;box-sizing:border-box}
html,body{width:874px;height:1200px;overflow:hidden}
body{font-family:"PT Sans",Arial,sans-serif;color:var(--text);font-size:9px;position:relative;background:var(--sea)}
.abs{position:absolute}
.backdrop{left:0;top:0;width:874px;height:1024px;background:linear-gradient(180deg,var(--sky-top) 0%,var(--sky-mid) 28%,#6fb4dd 45%,var(--sea) 70%,var(--deep) 100%)}
.logo{left:82px;top:40px;color:var(--white);font-weight:700;font-size:25px}
.contact{left:452px;top:8px;color:var(--white)}
.contact .hot{position:absolute;left:21px;top:0;font-size:15px;white-space:nowrap}
.contact .line{position:absolute;left:21px;font-size:11px;white-space:nowrap}
.lang{left:697px;top:30px;width:110px;height:20px;background:var(--white);border:1px solid #ccc;font-size:8px;color:#999;padding:4px 0 0 26px}
.lang .flag{position:absolute;left:6px;top:5px;width:14px;height:9px;background:#2b3f8e}
.lang svg{position:absolute;right:6px;top:7px}
.nav{left:579px;top:70px;width:226px;height:24px;background:var(--nav);display:flex;font-size:9.5px;color:var(--white)}
.nav span{padding:6px 9px 0}
.nav .active{background:var(--nav-active);padding:6px 13px 0}
.frame{left:73px;top:97px;width:736px;height:920px;background:var(--frame);border-radius:3px}
.hero{left:81px;top:105px;width:720px;height:317px;background:linear-gradient(180deg,#2e5fcf 0%,#6aa6e6 55%,#8fd0e8 75%,#f2f0e6 100%);border:2px solid #7a8fa8}
.slide-arrow{width:14px;height:28px;background:#222;border-radius:2px;top:246px}
.slide-arrow svg{position:absolute;left:4px;top:10px}
.tab{top:125px;height:31px;font-size:15px;text-align:center;padding-top:7px;color:var(--white);background:#2c2c2c;border-radius:3px 3px 0 0}
.tab.on{background:var(--white);color:var(--orange)}
.form{left:111px;top:156px;width:307px;height:158px;background:var(--white);border-radius:0 0 3px 3px;box-shadow:0 1px 3px rgba(0,0,0,.3)}
.lbl{font-size:8.5px;color:#444}
.field{height:24px;border:1px solid #bbb;border-radius:3px;background:var(--white);box-shadow:inset 0 1px 2px rgba(0,0,0,.1)}
.check{width:9px;height:9px;border:1px solid #777;background:var(--white)}
.btn-search{left:267px;top:272px;width:96px;height:24px;background:linear-gradient(180deg,#ffc33a,var(--orange-dark));border-radius:3px;font-size:12px;color:#222;text-align:center;padding-top:4px;box-shadow:2px 2px 3px rgba(0,0,0,.4)}
.calendar{left:111px;top:327px;width:307px;height:78px;background:var(--white);border-radius:3px;display:flex;overflow:hidden;box-shadow:0 1px 3px rgba(0,0,0,.3)}
.day{flex:1;font-size:8.5px;padding:22px 0 0;text-align:center;color:#222}
.day.alt{background:#e2e4ea}
.cal-month{left:118px;top:333px;font-size:8.5px;color:#222}
.panel{left:80px;top:422px;width:722px;height:587px;background:var(--white)}
.basket{left:91px;top:439px;width:188px;height:195px;border-radius:6px;overflow:hidden;box-shadow:0 3px 5px rgba(0,0,0,.3)}
.basket .head{height:84px;background:linear-gradient(180deg,#5b9ae0,var(--basket));color:var(--white);font-family:"PT Sans Narrow",sans-serif;font-weight:700;font-size:15px;padding:10px 0 0 46px}
.basket .row{height:37px;background:linear-gradient(180deg,#8fd03a,var(--green-dark));border-top:1px solid #b6e27a;color:var(--white);font-family:"PT Sans Narrow",sans-serif;font-weight:700;font-size:15px;padding:7px 0 0 32px}
.tour{left:91px;top:659px;width:188px;height:175px;border:1px solid #ccc;border-radius:4px;background:linear-gradient(180deg,#fff,#f1f1f1)}
.tour h4{position:absolute;left:38px;top:13px;font-family:"PT Sans Narrow",sans-serif;font-size:12px;color:#222}
.tour .rule{position:absolute;left:8px;top:34px;width:172px;height:2px;background:#ccc}
.btn-login{left:207px;top:798px;width:64px;height:24px;background:linear-gradient(180deg,#8fd03a,var(--green-dark));border-radius:5px;color:var(--white);font-family:"PT Sans Narrow",sans-serif;font-weight:700;font-size:12px;text-align:center;padding-top:4px}
.sec-title{font-family:"PT Sans Narrow",sans-serif;font-weight:700;font-size:16px;color:var(--cyan)}
.card{left:304px;width:474px;border:1px solid var(--line);border-radius:3px;background:linear-gradient(180deg,#fff,#f7f7f7);box-shadow:0 1px 3px rgba(0,0,0,.12)}
.card h3{position:absolute;left:12px;top:9px;font-family:"PT Sans Narrow",sans-serif;font-weight:700;font-size:12px;color:var(--orange)}
.card p{position:absolute;font-size:8.5px;line-height:10.3px;color:#333;text-align:justify}
.btn-view{right:8px;width:74px;height:22px;background:var(--navy);border-radius:3px;color:var(--white);font-family:"PT Sans Narrow",sans-serif;font-weight:700;font-size:9.5px;text-align:center;padding-top:5px}
.footer{left:0;top:1024px;width:874px;height:176px;background:var(--footer);color:var(--white)}
.footer .band{position:absolute;left:0;top:100px;width:874px;height:76px;background:var(--footer-dark);border-top:1px solid #2f62b4}
.f-head{font-size:10px}
.f-text{font-size:8.5px;line-height:11.7px}
.email{left:640px;top:1058px;width:162px;height:20px;background:var(--white);border:1px solid #aaa;color:#333;font-size:8px;padding:4px 0 0 13px}
.btn-send{left:754px;top:1090px;width:49px;height:23px;background:linear-gradient(180deg,#8fd03a,var(--green-dark));border-radius:5px;font-family:"PT Sans Narrow",sans-serif;font-weight:700;font-size:12px;text-align:center;padding-top:4px;color:var(--white)}
.social{top:1150px;width:19px;height:19px;border-radius:2px;background:#5b7fb8}
</style>
</head>
<body>
<div class="abs backdrop" role="img" aria-label="Tropical beach photograph with palm trees, blue sea and water bungalows"></div>

<div class="abs logo">Belvasco Travel</div>

<div class="abs contact">
  <svg class="abs" style="left:0;top:4px" width="17" height="20" viewBox="0 0 17 20"><path d="M3 1c2-1 3 0 4 3s0 3-1 4c1 3 3 5 5 7 1-1 2-2 4 0s1 3-1 4C8 20-1 8 3 1z" fill="#fff"/></svg>
  <div class="hot">8-800-555-0142</div>
  <div class="line" style="top:22px">Phone: +7 (495) 555-01-27</div>
  <div class="line" style="top:41px">(Mon-Fri) Hours: 9:00 am - 18:00</div>
</div>

<div class="abs lang"><span class="flag"></span>English<svg width="6" height="4" viewBox="0 0 6 4"><path d="M0 0h6L3 4z" fill="#444"/></svg></div>

<nav class="abs nav"><span class="active">Home</span><span>About Us</span><span>Forum</span><span>Contact Us</span></nav>

<div class="abs frame"></div>
<div class="abs hero" role="img" aria-label="Photograph of a palm tree leaning over a small white sand island under a blue sky"></div>
<div class="abs slide-arrow" style="left:82px"><svg width="6" height="8" viewBox="0 0 6 8"><path d="M5 0L1 4l4 4" stroke="#fff" fill="none"/></svg></div>
<div class="abs slide-arrow" style="left:786px"><svg width="6" height="8" viewBox="0 0 6 8"><path d="M1 0l4 4-4 4" stroke="#fff" fill="none"/></svg></div>

<div class="abs tab on" style="left:111px;width:102px">TICKETS</div>
<div class="abs tab" style="left:218px;width:98px">INFO</div>
<div class="abs tab" style="left:320px;width:98px">HOTELS</div>

<div class="abs form"></div>
<div class="abs lbl" style="left:124px;top:164px">Whence</div>
<div class="abs lbl" style="left:270px;top:164px">Where</div>
<div class="abs field" style="left:121px;top:181px;width:130px"></div>
<div class="abs field" style="left:267px;top:181px;width:130px"></div>
<div class="abs lbl" style="left:124px;top:211px">There</div>
<div class="abs lbl" style="left:270px;top:211px">Back</div>
<div class="abs field" style="left:121px;top:227px;width:130px"></div>
<svg class="abs" style="left:231px;top:233px" width="12" height="11" viewBox="0 0 12 11"><rect x=".5" y="1.5" width="11" height="9" fill="#fff" stroke="#999"/><rect x=".5" y="1.5" width="11" height="3" fill="#d33"/></svg>
<div class="abs field" style="left:267px;top:227px;width:72px"></div>
<div class="abs check" style="left:351px;top:226px"></div>
<div class="abs lbl" style="left:366px;top:224px">Back</div>
<div class="abs check" style="left:351px;top:242px"></div>
<svg class="abs" style="left:352px;top:241px" width="9" height="9" viewBox="0 0 9 9"><path d="M1 4.5l2.5 2.5L8 1.5" stroke="#2a9a3a" stroke-width="1.6" fill="none"/></svg>
<div class="abs lbl" style="left:366px;top:241px">One way</div>
<div class="abs lbl" style="left:124px;top:259px">Class</div>
<div class="abs field" style="left:121px;top:276px;width:130px"></div>
<svg class="abs" style="left:233px;top:283px" width="10" height="10" viewBox="0 0 10 10"><rect width="10" height="10" rx="2" fill="#c9d8f0"/><path d="M2 4l3 3 3-3" stroke="#3a5fa8" stroke-width="1.4" fill="none"/></svg>
<div class="abs btn-search">Search</div>

<div class="abs calendar">
  <div class="day" style="flex:.9">Thu, 01</div><div class="day alt" style="flex:.75">Fri, 02</div><div class="day" style="flex:.9">Sat, 03</div><div class="day alt" style="flex:.9">Sun, 04</div><div class="day" style="flex:1">Mon, 05</div><div class="day alt" style="flex:.85">Tue, 06</div><div class="day" style="flex:1">Wed, 07</div>
</div>
<div class="abs cal-month">January</div>

<div class="abs panel"></div>

<div class="abs basket">
  <div class="head">BASKET
    <svg style="position:absolute;left:50px;top:36px" width="36" height="32" viewBox="0 0 36 32"><path d="M2 3h6l5 17h17l4-12H10" stroke="#333" stroke-width="2" fill="none"/><path d="M11 11h21M12 15h19" stroke="#777"/><circle cx="14" cy="26" r="3" fill="#333"/><circle cx="28" cy="26" r="3" fill="#333"/></svg>
  </div>
  <div class="row">EMPTY</div>
  <div class="row">PAYMENT</div>
  <div class="row" style="font-weight:400">Pricing</div>
</div>

<div class="abs tour">
  <svg class="abs" style="left:14px;top:7px" width="20" height="22" viewBox="0 0 20 22"><rect x="4" y="2" width="12" height="3" fill="#222"/><rect x="2" y="5" width="16" height="2" fill="#222"/><rect x="3" y="13" width="14" height="9" rx="2" fill="#333"/></svg>
  <h4>MY TOUR</h4>
  <div class="rule"></div>
  <div class="abs lbl" style="left:17px;top:45px">Name</div>
  <div class="abs field" style="left:10px;top:58px;width:168px;height:20px;border-radius:0"></div>
  <div class="abs lbl" style="left:17px;top:91px">Email</div>
  <div class="abs field" style="left:11px;top:105px;width:168px;height:20px;border-radius:0"></div>
</div>
<div class="abs btn-login">LOGIN</div>

<svg class="abs" style="left:312px;top:442px" width="23" height="21" viewBox="0 0 23 21"><rect x=".5" y=".5" width="22" height="20" fill="#fff" stroke="#2a7cc8"/><rect x=".5" y=".5" width="22" height="4" fill="#2a7cc8"/><path d="M4 8h15M4 11h15M4 14h15M4 17h15" stroke="#2a7cc8"/></svg>
<div class="abs sec-title" style="left:346px;top:444px">INFO</div>
<div class="abs card" style="top:474px;height:173px">
  <h3>There are two options apply for a visa</h3>
  <p style="left:20px;top:39px;font-size:9px">1.Oformlenie visa "Online"</p>
  <p style="left:254px;top:39px;font-size:9px">2. Visa "Myself."</p>
  <p style="left:20px;top:62px;width:191px">Cmozhete you apply for a visa, send and receive back their documents "from the comfort of home!"</p>
  <p style="left:254px;top:62px;width:191px">With this service, your presence is required at the visa application center. The service is free, but you need to press the "Select" and then on "Payment" ($ 0).</p>
  <p style="left:20px;top:114px;width:430px;text-align:left">After booking, the selected service, you need to fill out a simple form on the visa application form on the newly created for your personal page.<br>finish filling out the form pdf-file forms will be created automatically.</p>
  <div class="abs btn-view" style="top:142px">View All &gt;&gt;</div>
</div>

<svg class="abs" style="left:312px;top:662px" width="26" height="24" viewBox="0 0 26 24"><path d="M25 1L1 10l8 3 2 9 4-6 6 3z" fill="#1c5fb0"/></svg>
<div class="abs sec-title" style="left:345px;top:665px">TICKETS</div>
<div class="abs card" style="top:693px;height:122px">
  <h3>Flights from Tours designer.</h3>
  <p style="left:14px;top:34px;width:450px">On our site you can consider offers from different airlines and purchase tickets according to your wishes and budget.<br>Plan dates of departures and arrivals c in any country, filling the cells you want, Tour Designer automatically displays your program in the calendar.<br>On Tour Designer You can create any tour, including round-the-world and pay for all the services a single payment.</p>
  <div class="abs btn-view" style="top:95px">View All &gt;&gt;</div>
</div>

<svg class="abs" style="left:312px;top:830px" width="20" height="20" viewBox="0 0 20 20"><path d="M10 1L1 9h3v10h12V9h3z" fill="#1c5fb0"/><rect x="8" y="12" width="4" height="7" fill="#fff"/></svg>
<div class="abs sec-title" style="left:337px;top:833px">HOTELS</div>
<div class="abs card" style="top:862px;height:121px">
  <h3>Hotels by City Builder.</h3>
  <p style="left:14px;top:34px;width:450px">Our site offers a wide selection of hotels located in different countries and continents of the world. You can choose and book all kinds of accommodation options, according to your wishes and budget.<br>pursue their dreams!<br>We have created for you the most convenient framework for planning a vacation or business trip. Tour Builder saves your time now to buy a package tour you can just 3 simple steps:<br>Choose the services Confirm requested services, payment of a single payment.</p>
  <div class="abs btn-view" style="top:95px">View All &gt;&gt;</div>
</div>

<footer class="abs footer">
  <div class="band"></div>
</footer>
<div class="abs f-head" style="left:80px;top:1035px;color:#fff">FIND US</div>
<div class="abs f-text" style="left:81px;top:1061px;color:#fff">Sunkettle Tours Limited<br>14 Harbour Row<br>London, E2 7QX<br>UK</div>
<svg class="abs" style="left:213px;top:1062px" width="16" height="12" viewBox="0 0 16 12"><path d="M1 4c0-3 14-3 14 0v1h-4V3H5v2H1z M3 6h10l1 6H2z" fill="#cfd8e8"/></svg>
<div class="abs f-text" style="left:237px;top:1061px;color:#fff">+7 (495) 555-01-27</div>
<svg class="abs" style="left:213px;top:1083px" width="16" height="11" viewBox="0 0 16 11"><rect x=".5" y=".5" width="15" height="10" fill="none" stroke="#cfd8e8"/><path d="M.5.5l7.5 6 7.5-6" stroke="#cfd8e8" fill="none"/></svg>
<div class="abs f-text" style="left:237px;top:1083px;color:#fff">info@sunkettle.com</div>
<div class="abs f-head" style="left:398px;top:1038px;color:#fff">VIEW SITE</div>
<div class="abs f-text" style="left:398px;top:1060px;color:#fff">Home<br>About Us<br>Forum<br>Contacts</div>
<div class="abs f-head" style="left:516px;top:1038px;color:#fff">HELP</div>
<div class="abs f-text" style="left:516px;top:1060px;color:#fff">Help<br>Terms of use<br>Privacy Policy<br>Cookies</div>
<div class="abs f-head" style="left:640px;top:1038px;color:#fff">EXCLUSIVE OFFERS</div>
<div class="abs email">Email</div>
<div class="abs btn-send">SEND</div>

<div class="abs social" style="left:87px"></div>
<div class="abs social" style="left:115px"></div>
<div class="abs social" style="left:143px"></div>
<div class="abs social" style="left:171px"></div>
<div class="abs social" style="left:199px"></div>
<div class="abs social" style="left:227px"></div>
<div class="abs social" style="left:256px"></div>
<div class="abs f-text" style="left:641px;top:1146px;color:#fff;font-size:8px">© 2013 &nbsp;belvascotravel.com, All rights reserved.</div>
</body>
</html>
```